Need a website setup for our new removalist business.
Our business is called Harbour Lane Removals and would like a website setup.
We don’t have a website, logo or design as of yet. Our truck is blue so something possibly that works and can incorporate the blue.

```html
<!DOCTYPE html>
<html lang="en">
<head>
<meta charset="utf-8">
<title>Harbour Lane Removals</title>
<link href="https://fonts.googleapis.com/css2?family=Russo+One&family=Roboto:ital,wght@0,400;0,500;0,700;1,400&display=swap" rel="stylesheet">
<style>
:root{
  --blue:#1d6ff2;
  --blue-dark:#1559c8;
  --ink:#111111;
  --text:#555a63;
  --pale:#eaf1fd;
  --footer:#121212;
  --white:#ffffff;
  --line:#8a8f98;
  --star:#f5b400;
}
*{box-sizing:border-box;margin:0;padding:0}
html,body{width:1200px;height:3454px;overflow:hidden}
body{position:relative;font-family:"Roboto",Arial,sans-serif;color:var(--text);background:var(--white)}
.abs{position:absolute}
.heading{font-family:"Russo One",Impact,sans-serif;color:var(--ink);text-transform:uppercase;letter-spacing:.5px}
.btn{position:absolute;display:flex;align-items:center;justify-content:center;background:var(--blue);color:var(--white);font-size:14px;font-weight:500;border-radius:2px}
.photo{position:absolute}
p.body{font-size:13.4px;line-height:21.5px;text-align:justify}

/* top bar */
.topbar{left:0;top:0;width:1200px;height:40px;background:var(--blue);color:var(--white);font-size:14px;font-weight:500}
.topbar span{position:absolute;top:11px;display:flex;align-items:center;gap:8px}
/* header */
.header{left:0;top:40px;width:1200px;height:73px;background:var(--white)}
.brand{position:absolute;display:flex;align-items:center;gap:10px;font-family:"Russo One",sans-serif;font-size:19px}
.brand i{display:block;width:16px;height:16px;background:var(--blue)}
.nav{position:absolute;left:484px;top:0;height:73px;display:flex}
.nav a{display:flex;align-items:center;padding:0 15px;height:73px;border-left:1px solid #e2e2e2;font-size:14.5px;font-weight:500;color:var(--ink);text-decoration:none}
.nav a.active{color:var(--blue)}
.nav a.search{border-right:1px solid #e2e2e2;padding:0 22px}
.quote{position:absolute;left:935px;top:15px;width:120px;height:40px;background:var(--ink);color:var(--white);font-size:14px;font-weight:500;display:flex;align-items:center;justify-content:center;border-radius:3px}
/* hero */
.hero{left:0;top:113px;width:1200px;height:520px;background:linear-gradient(90deg,#4c5a52 0%,#6d7468 38%,#8b7a5f 60%,#a88a60 100%)}
.hero .kicker{left:142px;top:152px;font-size:26px;color:var(--white)}
.hero .title{left:142px;top:180px;font-size:40px;color:var(--white)}
.hero p{position:absolute;left:142px;top:243px;width:325px;color:var(--white);font-size:13.4px;line-height:21.5px}
.arrow-dot{position:absolute;top:432px;width:36px;height:36px;border-radius:50%;display:flex;align-items:center;justify-content:center}
/* about */
.stat{left:599px;top:952px;width:238px;height:178px;background:var(--blue);color:var(--white);text-align:center}
.stat b{display:block;font-family:"Russo One",sans-serif;font-size:40px;font-weight:400;margin-top:42px}
.stat span{font-size:20px;line-height:26px}
/* services */
.icon-ring{position:absolute;width:112px;height:112px;border-radius:50%;background:var(--blue);border:7px solid #8db4f7;display:flex;align-items:center;justify-content:center}
.svc-title{font-family:"Roboto",sans-serif;font-size:27px;font-weight:500;color:var(--ink)}
/* testimonials */
.testi{left:0;top:2081px;width:1200px;height:456px;background:var(--pale)}
.card{position:absolute;top:155px;width:288px;height:204px;background:var(--white);border-radius:6px;padding:0 20px}
.card.active{box-shadow:0 6px 14px rgba(29,111,242,.18);border-bottom:6px solid var(--blue)}
.card .q{position:absolute;top:-10px;left:20px;font-family:"Russo One",sans-serif;font-size:34px;color:var(--blue)}
.card .stars{position:absolute;top:22px;left:20px;color:var(--star);font-size:14px;letter-spacing:2px}
.card p{position:absolute;top:44px;left:20px;right:20px;font-size:13.2px;line-height:21.5px;font-style:italic;text-align:justify}
.person{position:absolute;top:136px;left:20px;display:flex;align-items:center;gap:9px}
.person i{display:block;width:46px;height:46px;border-radius:50%;background:#c7d7f2;border:2px solid var(--blue)}
.person b{display:block;color:var(--ink);font-size:15.5px;font-weight:500}
.person small{font-size:12.5px;color:#777}
/* contact */
.info{left:143px;top:2637px;width:361px;height:354px;border-radius:10px;background:linear-gradient(160deg,#2a7bf5,#1b66e6)}
.info-row{position:absolute;left:60px;display:flex;gap:14px;color:var(--white)}
.info-row .ic{width:50px;height:50px;border:2px solid rgba(255,255,255,.85);border-radius:50%;display:flex;align-items:center;justify-content:center;flex:none}
.info-row b{display:block;font-size:19px;font-weight:500;margin-top:2px}
.info-row span{font-size:14px}
.field{position:absolute;border-bottom:1.5px solid #555;font-size:13.4px;color:#666;padding-bottom:5px}
/* footer */
.footer{left:0;top:3098px;width:1200px;height:356px;background:var(--footer);color:var(--white)}
.footer h4{position:absolute;top:88px;font-size:20px;font-weight:700;letter-spacing:.3px}
.links{position:absolute;top:132px;list-style:none;font-size:16px}
.links li{height:32px;display:flex;align-items:center;gap:12px}
.links li:before{content:"»";color:var(--blue);font-size:16px}
.social{position:absolute;top:139px;width:26px;height:26px;border-radius:50%;background:#3a3a3a}
.news{left:783px;top:128px;width:272px;height:42px;border:1px solid #444;background:#1c1c1c;font-size:12.5px;display:flex;align-items:center;justify-content:space-between;padding:0 16px}
</style>
</head>
<body>

<div class="abs topbar">
  <span style="left:143px"><svg width="14" height="11" viewBox="0 0 14 11"><rect x="0.5" y="0.5" width="13" height="10" rx="1" fill="#fff"/><path d="M1 1l6 5 6-5" stroke="#1d6ff2" stroke-width="1.4" fill="none"/></svg>hello@harbourlane.example</span>
  <span style="left:886px"><svg width="13" height="13" viewBox="0 0 24 24"><path fill="#fff" d="M6.6 10.8a15 15 0 006.6 6.6l2.2-2.2c.3-.3.7-.4 1-.2 1.1.4 2.3.6 3.6.6.6 0 1 .4 1 1V20c0 .6-.4 1-1 1A17 17 0 013 4c0-.6.4-1 1-1h3.5c.6 0 1 .4 1 1 0 1.3.2 2.5.6 3.6.1.3 0 .7-.2 1z"/></svg>Call : +1 555 014 2290</span>
</div>

<header class="abs header">
  <div class="brand" style="left:143px;top:25px;color:var(--ink)"><i></i>HARBOUR LANE REMOVALS</div>
  <nav class="nav">
    <a class="active">Home</a><a>Services</a><a>About Us</a><a>Blog</a><a>Contact</a>
    <a class="search"><svg width="14" height="14" viewBox="0 0 14 14"><circle cx="6" cy="6" r="4.5" stroke="#1d6ff2" stroke-width="2" fill="none"/><path d="M9.5 9.5L13 13" stroke="#1d6ff2" stroke-width="2"/></svg></a>
  </nav>
  <div class="quote">Get A Quote</div>
</header>

<section class="abs hero" role="img" aria-label="Smiling removalist in a blue polo wheeling boxes out of a truck beside a house">
  <div class="abs heading kicker">Move smarter with</div>
  <div class="abs heading title">Harbour Lane</div>
  <p>Lorem ipsum dolor sit amet, consectetur adipiscing elit, sed do eiusmod tempor incididunt ut labore et dolore magna aliqua.</p>
  <div class="btn" style="left:143px;top:321px;width:120px;height:38px">Discover More</div>
  <div class="arrow-dot" style="left:557px;background:#fff"><svg width="10" height="12" viewBox="0 0 10 12"><path d="M7 1L2 6l5 5" stroke="#1d6ff2" stroke-width="2" fill="none"/></svg></div>
  <div class="arrow-dot" style="left:605px;background:var(--blue)"><svg width="10" height="12" viewBox="0 0 10 12"><path d="M3 1l5 5-5 5" stroke="#fff" stroke-width="2" fill="none"/></svg></div>
</section>

<!-- About -->
<h2 class="abs heading" style="left:142px;top:708px;font-size:38px">About Us</h2>
<p class="abs body" style="left:142px;top:765px;width:421px">Lorem ipsum dolor sit amet, consectetur adipiscing elit, sed do eiusmod tempor incididunt ut labore et dolore magna aliqua. Ut enim ad minim veniam, quis nostrud exercitation ullamco laboris nisi ut aliquip ex ea commodo consequat. Duis aute irure dolor in reprehenderit in voluptate velit esse cillum dolore eu fugiat nulla pariatur. Excepteur sint occaecat cupidatat non proident, sunt in culpa qui officia deserunt mollit anim id est laborum.</p>
<p class="abs body" style="left:142px;top:937px;width:421px">Sed ut perspiciatis unde omnis iste natus error sit voluptatem accusantium doloremque laudantium, totam rem aperiam, eaque ipsa quae ab illo inventore veritatis et quasi architecto beatae vitae dicta sunt explicabo. Nemo enim ipsam voluptatem quia voluptas sit aspernatur aut odit aut fugit, sed quia consequuntur magni dolores eosqui ratione voluptatem sequi nesciunt</p>
<div class="btn" style="left:143px;top:1082px;width:120px;height:40px">Learn More</div>

<div class="abs" style="left:951px;top:633px;width:249px;height:192px;background:var(--blue)"></div>
<div class="photo" style="left:701px;top:740px;width:250px;height:205px;background:linear-gradient(160deg,#b9c6cf,#7d8f6a 55%,#a49a88)" role="img" aria-label="Two movers carrying a wrapped item up a garden path"></div>
<div class="photo" style="left:951px;top:825px;width:249px;height:232px;background:linear-gradient(150deg,#dfe5ea,#9aa6b3 60%,#6f7c8c)" role="img" aria-label="Smiling mover in a cap holding a box"></div>
<div class="photo" style="left:843px;top:945px;width:108px;height:185px;background:linear-gradient(180deg,#b3a79a,#8d8378)" role="img" aria-label="Paved path continuing from the garden scene"></div>
<div class="abs stat"><b>20</b><span>Years<br>Experience</span></div>

<!-- Services -->
<h2 class="abs heading" style="left:0;top:1236px;width:1200px;text-align:center;font-size:38px">Our Services</h2>

<div class="photo" style="left:0;top:1303px;width:599px;height:389px;background:linear-gradient(120deg,#a79484,#d9cbbb 50%,#c7b49c)" role="img" aria-label="Two movers in blue overalls packing a plant, sofa and boxes in a living room"></div>
<div class="icon-ring" style="left:543px;top:1344px"><svg width="48" height="44" viewBox="0 0 48 44" fill="none" stroke="#fff" stroke-width="2"><path d="M4 22L24 4l20 18"/><path d="M9 18v23h30V18"/><rect x="20" y="27" width="8" height="14"/><rect x="30" y="22" width="6" height="6"/></svg></div>
<div class="abs svc-title" style="left:677px;top:1356px">RESIDENTIAL</div>
<p class="abs body" style="left:677px;top:1400px;width:379px">Lorem ipsum dolor sit amet, consectetur adipiscing elit, sed do eiusmod tempor incididunt ut labore et dolore magna aliqua. Ut enim ad minim veniam, quis nostrud exercitation ullamco laboris nisi ut aliquip ex ea commodo consequat. Duis aute irure dolor in reprehenderit in voluptate velit esse cillum dolore eu fugiat nulla pariatur. Excepteur sint occaecat cupidatat non proident, sunt in culpa qui officia deserunt mollit anim id est laborum. Sed ut perspiciatis unde omnis iste natus error sit voluptatem accusantium doloremque</p>
<div class="btn" style="left:678px;top:1609px;width:120px;height:40px">Learn More</div>

<div class="photo" style="left:598px;top:1692px;width:602px;height:389px;background:linear-gradient(140deg,#cfcac3,#c4a57c 50%,#e4e1dc)" role="img" aria-label="Office with stairs, stacked cardboard boxes and wrapped furniture"></div>
<div class="icon-ring" style="left:542px;top:1733px"><svg width="48" height="46" viewBox="0 0 48 46" fill="none" stroke="#fff" stroke-width="2"><rect x="6" y="10" width="16" height="32"/><rect x="22" y="4" width="14" height="38"/><rect x="36" y="18" width="8" height="24"/><path d="M10 16h8M10 22h8M10 28h8M26 10h6M26 16h6M26 22h6M26 28h6M2 42h44"/></svg></div>
<div class="abs svc-title" style="left:142px;top:1745px;width:378px;text-align:right">COMMERCIAL</div>
<p class="abs body" style="left:142px;top:1789px;width:378px;text-align-last:right">Lorem ipsum dolor sit amet, consectetur adipiscing elit, sed do eiusmod tempor incididunt ut labore et dolore magna aliqua. Ut enim ad minim veniam, quis nostrud exercitation ullamco laboris nisi ut aliquip ex ea commodo consequat. Duis aute irure dolor in reprehenderit in voluptate velit esse cillum dolore eu fugiat nulla pariatur. Excepteur sint occaecat cupidatat non proident, sunt in culpa qui officia deserunt mollit anim id est laborum. Sed ut perspiciatis unde omnis iste natus error sit voluptatem accusantium doloremque</p>
<div class="btn" style="left:400px;top:1998px;width:120px;height:40px">Learn More</div>

<!-- Testimonials -->
<section class="abs testi">
  <h2 class="abs heading" style="left:0;top:72px;width:1200px;text-align:center;font-size:38px">Testimonials</h2>
  <svg class="abs" style="left:56px;top:256px" width="32" height="18" viewBox="0 0 32 18"><path d="M31 9H2M9 2L2 9l7 7" stroke="#111" stroke-width="2" fill="none"/></svg>
  <svg class="abs" style="left:1112px;top:256px" width="32" height="18" viewBox="0 0 32 18"><path d="M1 9h29M23 2l7 7-7 7" stroke="#111" stroke-width="2" fill="none"/></svg>

  <div class="card" style="left:143px"><div class="q">“</div><div class="stars">★★★★★</div><p>Lorem ipsum dolor sit amet, consectetur adipiscing elit, sed do eiusmod tempor incididunt ut labore et dolore magna aliqua. Ut enim ad minim veniam</p><div class="person"><i></i><div><b>John Doe</b><small>Company name</small></div></div></div>
  <div class="card active" style="left:456px;height:210px"><div class="q">“</div><div class="stars">★★★★★</div><p>Lorem ipsum dolor sit amet, consectetur adipiscing elit, sed do eiusmod tempor incididunt ut labore et dolore magna aliqua. Ut enim ad minim veniam</p><div class="person"><i></i><div><b>John Doe</b><small>Company name</small></div></div></div>
  <div class="card" style="left:768px"><div class="q">“</div><div class="stars">★★★★★</div><p>Lorem ipsum dolor sit amet, consectetur adipiscing elit, sed do eiusmod tempor incididunt ut labore et dolore magna aliqua. Ut enim ad minim veniam</p><div class="person"><i></i><div><b>John Doe</b><small>Company name</small></div></div></div>
</section>

<!-- Contact -->
<div class="abs info" role="group" aria-label="Contact details">
  <div class="info-row" style="top:40px"><div class="ic"><svg width="16" height="20" viewBox="0 0 16 20"><path d="M8 1a6 6 0 00-6 6c0 5 6 12 6 12s6-7 6-12a6 6 0 00-6-6z" fill="none" stroke="#fff" stroke-width="2"/><circle cx="8" cy="7" r="2" fill="#fff"/></svg></div><div><b>Address :</b><span>123, Lorem ipsum, Australia</span></div></div>
  <div class="info-row" style="top:143px"><div class="ic"><svg width="18" height="14" viewBox="0 0 18 14"><rect x="1" y="1" width="16" height="12" rx="1" fill="#fff"/><path d="M1 2l8 6 8-6" stroke="#1d6ff2" stroke-width="1.6" fill="none"/></svg></div><div><b>Email Address :</b><span>hello@harbourlane.example</span></div></div>
  <div class="info-row" style="top:246px"><div class="ic"><svg width="18" height="18" viewBox="0 0 24 24"><path fill="#fff" d="M6.6 10.8a15 15 0 006.6 6.6l2.2-2.2c.3-.3.7-.4 1-.2 1.1.4 2.3.6 3.6.6.6 0 1 .4 1 1V20c0 .6-.4 1-1 1A17 17 0 013 4c0-.6.4-1 1-1h3.5c.6 0 1 .4 1 1 0 1.3.2 2.5.6 3.6.1.3 0 .7-.2 1z"/></svg></div><div><b>Phone :</b><span>+1 555 014 2290</span></div></div>
</div>
<h2 class="abs heading" style="left:552px;top:2630px;font-size:38px">Contact Us</h2>
<div class="field" style="left:555px;top:2704px;width:233px">First name</div>
<div class="field" style="left:822px;top:2704px;width:235px">Last name</div>
<div class="field" style="left:555px;top:2769px;width:233px">Email</div>
<div class="field" style="left:822px;top:2769px;width:235px">Phone</div>
<div class="field" style="left:555px;top:2897px;width:500px">Message</div>
<div class="btn" style="left:554px;top:2948px;width:120px;height:41px;gap:6px">Submit <svg width="13" height="13" viewBox="0 0 14 14"><path d="M13 1L1 6l5 2 2 5z" fill="#fff"/></svg></div>

<!-- Footer -->
<footer class="abs footer">
  <div class="brand" style="left:143px;top:77px;color:var(--white)"><i></i>HARBOUR LANE REMOVALS</div>
  <span class="social" style="left:145px"></span>
  <span class="social" style="left:177px;background:#fff"></span>
  <span class="social" style="left:210px"></span>

  <h4 style="left:457px">QUICK LINKS</h4>
  <ul class="links" style="left:457px"><li>Home</li><li>About</li><li>Services</li><li>Contact</li></ul>
  <ul class="links" style="left:575px"><li>Terms and Condition</li><li>Privacy policy</li><li>Help</li><li>Support</li></ul>

  <h4 style="left:783px">SUBSCRIBE TO NEWSLETTER</h4>
  <div class="abs news"><span>Email address</span><svg width="15" height="15" viewBox="0 0 14 14"><path d="M13 1L1 6l5 2 2 5z" fill="#1d6ff2"/></svg></div>

  <div class="abs" style="left:143px;top:287px;width:914px;height:1px;background:#3a3a3a"></div>
  <div class="abs" style="left:0;top:310px;width:1200px;text-align:center;font-size:14px">© Copyrights 2024 | All Rights Reserved</div>
</footer>

</body>
</html>
```